Dental specialist needs a sharp looking letterhead

I am looking for a letterhead to be used to send letters and communication between myself (a dental specialist) and other dentists.
My office is a state of the art dental specialty office.
I need to letterhead to also state:
Bertram L. Oswick DDS
2748 Tollard Avenue, Suite K
West Tollard, NY 14391
(716)392-5061
fax: (716)392-5087
oswickroot.com (**this email address may change)

i included my logo designs.
thank you

Target Market(s)

dentists

Industry/Entity Type

Communication

Requirements
Must have
• the included logo, whether the vertical or horizontal versions

```html
<!DOCTYPE html>
<html lang="en">
<head>
<meta charset="utf-8">
<title>Keystone Endodontics P.C. – Letterhead</title>
<link rel="stylesheet" href="https://fonts.googleapis.com/css2?family=Didact+Gothic&family=Montserrat:wght@600;700&display=swap">
<style>
  :root {
    --backdrop: #dcdcdc;
    --paper: #f4f4f4;
    --ink: #2a2a2a;
    --ink-soft: #4a4a4a;
    --brand-blue: #1e9ad6;
    --brand-green: #6aa634;
    --rule: #5a5a5a;
  }
  * { margin: 0; padding: 0; box-sizing: border-box; }
  html, body {
    width: 1200px;
    height: 968px;
    overflow: hidden;
    background: var(--backdrop);
  }
  .letterhead {
    position: absolute;
    left: 245px;
    top: 24px;
    width: 710px;
    height: 920px;
    background: var(--paper);
    overflow: hidden;
    font-family: "Didact Gothic", sans-serif;
    color: var(--ink);
  }
  .brand {
    position: absolute;
    top: 44px;
    right: 70px;
    display: flex;
    align-items: center;
    gap: 10px;
  }
  .brand-mark {
    width: 26px;
    height: 26px;
    background: var(--brand-blue);
  }
  .brand-name {
    font-family: "Montserrat", sans-serif;
    font-weight: 600;
    color: var(--ink);
    line-height: 1.1;
  }
  .brand-name .primary { display: block; font-size: 20px; letter-spacing: 1px; }
  .brand-name .secondary { display: block; font-size: 10px; letter-spacing: 1.5px; text-align: right; }

  .sender {
    position: absolute;
    left: 0;
    right: 0;
    top: 790px;
    display: flex;
    flex-direction: column;
    align-items: center;
    text-align: center;
  }
  .sender-name {
    font-family: "Montserrat", sans-serif;
    font-weight: 700;
    font-size: 11px;
    letter-spacing: 0.5px;
    text-transform: uppercase;
    margin-bottom: 5px;
  }
  .sender-rule {
    width: 220px;
    height: 1px;
    background: var(--rule);
    margin-bottom: 7px;
  }
  .sender-contact {
    font-size: 9.5px;
    color: var(--ink-soft);
    margin-bottom: 5px;
    white-space: nowrap;
  }
  .sender-contact .label {
    color: var(--brand-blue);
    font-family: "Montserrat", sans-serif;
    font-weight: 600;
  }
  .sender-web {
    font-size: 9.5px;
    color: var(--ink-soft);
  }
  .sender-web .domain {
    color: var(--brand-blue);
    font-family: "Montserrat", sans-serif;
    font-weight: 600;
  }
  .base-stripe {
    position: absolute;
    left: 0;
    right: 0;
    bottom: 0;
  }
  .base-stripe .accent {
    height: 3px;
    background: var(--brand-blue);
    margin-bottom: 4px;
  }
  .base-stripe .band {
    height: 14px;
    background: var(--brand-green);
  }
</style>
</head>
<body>
  <main class="letterhead">
    <header class="brand">
      <span class="brand-mark" aria-hidden="true"></span>
      <span class="brand-name">
        <span class="primary">KEYSTONE</span>
        <span class="secondary">Endodontics P.C.</span>
      </span>
    </header>

    <footer class="sender">
      <p class="sender-name">Bertram L. Oswick DDS</p>
      <div class="sender-rule"></div>
      <p class="sender-contact">2748 Tollard Avenue, Suite K, West Tollard, NY 14391 · <span class="label">Phone:</span> (716) 392-5061 · <span class="label">Fax:</span> (716) 392-5087</p>
      <p class="sender-web">www.<span class="domain">oswickroot</span>.com</p>
    </footer>

    <div class="base-stripe" aria-hidden="true">
      <div class="accent"></div>
      <div class="band"></div>
    </div>
  </main>
</body>
</html>
```